Explosive, chemical reaction of creativity!

Web design for a digital marketing company. The unconventional is encouraged!
This is for a cool, young, geographically diverse company (sketchhive... you are all part of our team!!!)... we build websites but our real specialty is "search experience optimization".... creating conversion focused content, SEO (including content), and social media.

Target Market(s)

small to medium size businesses, law firms, medical practices, municipalities

Industry/Entity Type

Marketing

Number of Pages Required

2 page

Requirements
Must have
• WOW
• something different and special... we've been playing with a science theme (www.fernquillmedia.marketing) but we are open to different looks, layouts, etc.
• we nee a homepage design and an interior page design
• content needs to include: Marketing Catalysts (about us), Our Formula (services), Chemical Reactions(Results/Our Clients),
• FREE Online Prism Check
• Let us put together an objective snapshot of your digital presence for you.
Nice to have
• we are open to the use of background video (chemical reaction???)
• we are open to cool and different imagery
Should not have
• template look like most other websites

```html
<!DOCTYPE html>
<html lang="en">
<head>
<meta charset="utf-8">
<title>Fernquill Media Marketing</title>
<link rel="stylesheet" href="https://fonts.googleapis.com/css2?family=Open+Sans:wght@400;600;700&family=Oswald:wght@400&display=swap">
<style>
:root{
  --blue:#1d6db6;
  --blue-deep:#1e5895;
  --navy:#23599a;
  --ink:#3a3a3a;
  --muted:#555;
  --line:#c9c9c9;
  --paper:#ffffff;
  --mist:#f1f2f3;
  --ring:#dcdcdc;
}
*{margin:0;padding:0;box-sizing:border-box}
html,body{width:1200px;height:2624px;overflow:hidden;background:var(--paper)}
body{position:relative;font-family:"Open Sans",Arial,sans-serif;color:var(--ink)}
.abs{position:absolute}
.center{text-align:center}

/* header */
.site-header{left:0;top:0;width:1200px;height:84px;background:var(--paper)}
.brand{left:131px;top:24px;display:flex;align-items:center;gap:12px}
.brand-mark{width:30px;height:30px;background:var(--navy)}
.brand-name{font-weight:700;font-size:22px;color:var(--navy);letter-spacing:.5px}
.main-nav{left:497px;top:30px;display:flex;align-items:center;gap:0}
.main-nav a{font-size:11.5px;font-weight:600;color:#222;text-decoration:none;text-transform:uppercase;padding:7px 0;margin-right:34px}
.main-nav a.current{background:var(--blue);color:#fff;padding:7px 13px}

/* hero */
.hero{left:0;top:84px;width:1200px;height:493px;background:linear-gradient(120deg,#d9dde3 0%,#9fb3c8 35%,#5d86b8 60%,#c4cfdb 100%)}
.hero-caption{left:126px;top:362px;width:388px;height:168px;background:rgba(40,48,56,.75);color:#fff;font-size:30px;line-height:38px;padding:22px 34px}
.hero-arrow{top:316px;width:40px;height:54px}
.hero-dots{left:540px;top:532px;display:flex;gap:17px}
.hero-dots span{width:10px;height:10px;border-radius:50%;background:rgba(255,255,255,.8)}
.hero-dots span.on{background:transparent;border:2px solid #fff;width:13px;height:13px;margin-top:-1px}

/* offer band */
.offer{top:577px;height:158px;color:#fff;font-size:16px}
.offer-left{left:0;width:600px;background:var(--blue-deep)}
.offer-right{left:600px;width:600px;background:var(--blue)}
.offer svg{position:absolute;left:50%;transform:translateX(-50%)}
.offer p{position:absolute;left:0;width:100%;text-align:center;line-height:24px}

/* formula */
.phone{left:136px;top:787px;width:223px;height:464px;border-radius:34px;background:#0b0b12;border:4px solid #2a46b8}
.phone-screen{left:151px;top:852px;width:192px;height:338px;background:#fff}
.phone-art{left:165px;top:868px;width:164px;height:306px;background:radial-gradient(circle,#cfd6e4 0%,#ffffff 70%)}
.phone-brand{left:151px;top:995px;width:192px;text-align:center;font-weight:700;font-size:13px;color:#1b2a4a}
.phone-home{left:229px;top:1200px;width:36px;height:36px;border-radius:50%;border:2px solid #444}
.phone-speaker{left:222px;top:812px;width:50px;height:5px;border-radius:3px;background:#333}
.formula-title{left:402px;top:788px;font-size:23px;color:var(--blue);font-weight:400}
.formula-title b{font-weight:600}
.formula-sub{left:404px;top:824px;font-size:12px;color:var(--muted)}
.feature-icon{width:60px;height:60px;border-radius:50%;background:var(--blue)}
.feature-label{font-size:13px;font-weight:700;color:var(--blue-deep);text-transform:uppercase}
.feature-text{width:188px;font-size:11.5px;line-height:19px;color:var(--muted);text-align:justify}

/* data */
.data{left:0;top:1324px;width:1200px;height:439px;background:var(--mist)}
.data-title{left:0;top:1374px;width:1200px;font-size:24px;color:var(--blue)}
.data-title b{font-weight:700}
.data-sub{left:0;top:1407px;width:1200px;font-size:12px;color:var(--muted)}
.data-copy{left:210px;top:1445px;width:780px;font-size:12px;line-height:21px;color:var(--muted)}
.stat{width:240px;top:1519px}
.stat-label{width:240px;top:1648px;font-size:11.5px;line-height:19px;color:#333}
.stat-num{font-family:"Oswald",Arial,sans-serif;font-size:29px;fill:var(--blue)}
.btn{background:var(--blue);color:#fff;font-size:11px;font-weight:700;text-transform:uppercase;display:flex;align-items:center;justify-content:center;gap:8px}
.btn-lg{left:537px;top:1733px;width:129px;height:30px}

/* posts */
.divider-v{left:610px;top:1822px;width:1px;height:530px;background:var(--line)}
.divider-h{left:131px;top:2087px;width:938px;height:1px;background:var(--line)}
.post{width:440px;text-align:center}
.post-kicker{font-size:16px;color:var(--blue);line-height:22px}
.post-title{font-size:20px;font-weight:600;color:var(--blue);line-height:26px}
.post-text{font-size:11.5px;line-height:17px;color:var(--muted);margin:12px auto 0;width:330px}
.post .btn{width:86px;height:20px;margin:14px auto 0;font-size:9.5px}
.post svg{display:block;margin:0 auto 12px}

/* footer */
.site-footer{left:0;top:2415px;width:1200px;height:209px;background:var(--navy);color:#fff}
.follow{left:0;top:2449px;width:1200px;font-size:10px;font-weight:700;text-transform:uppercase}
.social{top:2474px;width:32px;height:32px;border-radius:50%}
.footer-nav{left:0;top:2541px;width:1200px;font-size:10.5px}
.copyright{left:0;top:2567px;width:1200px;font-size:10.5px}
</style>
</head>
<body>

<header class="site-header abs">
  <div class="brand abs"><span class="brand-mark"></span><span class="brand-name">FERNQUILL MEDIA</span></div>
  <nav class="main-nav abs">
    <a class="current">Home</a><a>Marketing Catalysts</a><a>Our Formula</a><a>Chemical Reactions</a><a>Contact</a>
  </nav>
</header>

<section class="hero abs" role="img" aria-label="Photo of a gloved scientist working with a petri dish in a laboratory"></section>
<svg class="hero-arrow abs" style="left:52px" viewBox="0 0 40 54"><path d="M30 4 L8 27 L30 50" fill="none" stroke="#fff" stroke-width="4" opacity=".85"/></svg>
<svg class="hero-arrow abs" style="left:1092px" viewBox="0 0 40 54"><path d="M10 4 L32 27 L10 50" fill="none" stroke="#fff" stroke-width="4" opacity=".85"/></svg>
<div class="hero-caption abs">It's not rocket science, it's Fernquill Media science!</div>
<div class="hero-dots abs"><span></span><span class="on"></span><span></span><span></span><span></span></div>

<section class="offer offer-left abs">
  <svg width="44" height="44" viewBox="0 0 44 44" style="top:32px"><path d="M16 5h12M18 5v13L7 38h30L26 18V5" fill="none" stroke="#fff" stroke-width="3"/><path d="M11 31h22" stroke="#fff" stroke-width="2"/></svg>
  <p style="top:92px"><b>FREE Online</b> Prism Check</p>
</section>
<section class="offer offer-right abs">
  <svg width="40" height="46" viewBox="0 0 40 46" style="top:24px"><rect x="6" y="8" width="28" height="34" rx="3" fill="none" stroke="#fff" stroke-width="3"/><rect x="14" y="3" width="12" height="8" fill="#fff"/><path d="M12 20h16M12 27h16M12 34h10" stroke="#fff" stroke-width="2.5"/></svg>
  <p style="top:82px">Let us put together an <b>objective snapshot</b><br>of your digital presence for you.</p>
</section>

<!-- formula -->
<div class="phone abs"></div>
<div class="phone-speaker abs"></div>
<div class="phone-screen abs"></div>
<div class="phone-art abs" role="img" aria-label="Illustration of blue molecule models around the company name"></div>
<div class="phone-brand abs">FERNQUILL MEDIA</div>
<div class="phone-home abs"></div>

<h2 class="formula-title abs">The <b>Perfect Digital Marketing</b> Formula!</h2>
<p class="formula-sub abs">Get the right message in front of the right people.</p>

<div class="feature-icon abs" style="left:404px;top:879px"><svg width="60" height="60" viewBox="0 0 60 60"><circle cx="30" cy="30" r="10" fill="none" stroke="#fff" stroke-width="2.5"/><path d="M20 30h20M30 20c-5 6-5 14 0 20M30 20c5 6 5 14 0 20" fill="none" stroke="#fff" stroke-width="2"/></svg></div>
<div class="feature-label abs" style="left:404px;top:961px">Website</div>
<p class="feature-text abs" style="left:404px;top:983px">You've got 10 seconds to grab the attention of a site viewer. We build for appearance, content, and functionality. It's a conversion causal nexus!</p>

<div class="feature-icon abs" style="left:642px;top:963px"><svg width="60" height="60" viewBox="0 0 60 60"><path d="M22 17h11l6 6v20H22z" fill="#fff"/><path d="M26 30h9M26 35h9" stroke="var(--blue)" stroke-width="2"/></svg></div>
<div class="feature-label abs" style="left:642px;top:1045px">Content</div>
<p class="feature-text abs" style="left:642px;top:1067px">Content is the most powerful element of our formula... it creates need, provokes emotion and sparks action.</p>

<div class="feature-icon abs" style="left:881px;top:1049px"><svg width="60" height="60" viewBox="0 0 60 60"><path d="M36 21L24 30l12 9" fill="none" stroke="#fff" stroke-width="2.5"/><circle cx="36" cy="21" r="5" fill="#fff"/><circle cx="24" cy="30" r="5" fill="#fff"/><circle cx="36" cy="39" r="5" fill="#fff"/></svg></div>
<div class="feature-label abs" style="left:881px;top:1131px">Social</div>
<p class="feature-text abs" style="left:881px;top:1153px">We are obsessed with the latest trends and are always testing new ways to cultivate both following and engagement.</p>

<svg class="abs" style="left:400px;top:1100px" width="680" height="170" viewBox="400 1100 680 170"><path d="M408 1109H591V1170H829V1259H1069" fill="none" stroke="var(--line)" stroke-width="1.5"/><circle cx="408" cy="1109" r="4.5" fill="#bbb"/><circle cx="1069" cy="1259" r="4.5" fill="#bbb"/></svg>

<!-- data -->
<section class="data abs" role="img" aria-label="Faint chemistry formulas and lab glassware sketches in the background"></section>
<h2 class="data-title abs center">Using <b>data</b> for success</h2>
<p class="data-sub abs center">Search Engine Optimization has been replaced with Search Experience Optimization</p>
<p class="data-copy abs center">SALES is the end result of everything we do. It is why companies exists. It's why we market. It's why your business is online. Our job is to help you maximize your opportunity online to build your brand, get found by new customers and, ultimately, generate SALES!</p>

<svg class="stat abs" style="left:90px" height="120" viewBox="0 0 240 120"><circle cx="120" cy="60" r="52" fill="none" stroke="var(--ring)" stroke-width="10"/><circle cx="120" cy="60" r="52" fill="none" stroke="var(--blue)" stroke-width="10" stroke-dasharray="303.9 326.7" transform="rotate(-90 120 60)"/><text class="stat-num" x="120" y="71" text-anchor="middle">93<tspan font-size="15">%</tspan></text></svg>
<svg class="stat abs" style="left:317px" height="120" viewBox="0 0 240 120"><circle cx="120" cy="60" r="52" fill="none" stroke="var(--ring)" stroke-width="10"/><circle cx="120" cy="60" r="52" fill="none" stroke="var(--blue)" stroke-width="10" stroke-dasharray="228.7 326.7" transform="rotate(-90 120 60)"/><circle cx="70.5" cy="76" r="9" fill="var(--blue)"/><text class="stat-num" x="120" y="71" text-anchor="middle">70<tspan font-size="15"> %</tspan></text></svg>
<svg class="stat abs" style="left:588px" height="120" viewBox="0 0 240 120"><circle cx="120" cy="60" r="52" fill="none" stroke="var(--ring)" stroke-width="10"/><circle cx="120" cy="60" r="52" fill="none" stroke="var(--blue)" stroke-width="10" stroke-dasharray="228.7 326.7" transform="rotate(-90 120 60)"/><circle cx="70.5" cy="76" r="9" fill="var(--blue)"/><text class="stat-num" x="120" y="71" text-anchor="middle">70<tspan font-size="15"> %</tspan></text></svg>
<svg class="stat abs" style="left:851px" height="120" viewBox="0 0 240 120"><circle cx="120" cy="60" r="52" fill="none" stroke="var(--ring)" stroke-width="10"/><circle cx="120" cy="60" r="52" fill="none" stroke="var(--blue)" stroke-width="10" stroke-dasharray="163.4 326.7" transform="rotate(-90 120 60)"/><text class="stat-num" x="120" y="71" text-anchor="middle">50<tspan font-size="15">%</tspan></text></svg>

<p class="stat-label abs center" style="left:90px">Online experiences begin<br>with a search engine</p>
<p class="stat-label abs center" style="left:317px">Of the links search users<br>click on are organic</p>
<p class="stat-label abs center" style="left:588px">Of US population has at least one<br>social networking profile</p>
<p class="stat-label abs center" style="left:851px">Of companies are using digital<br>marketing but don't have a plan.</p>

<div class="btn btn-lg abs">Read More <svg width="8" height="10" viewBox="0 0 8 10"><path d="M1 1l5 4-5 4" fill="none" stroke="#fff" stroke-width="2"/></svg></div>

<!-- posts -->
<div class="divider-v abs"></div>
<div class="divider-h abs"></div>

<article class="post abs" style="left:147px;top:1832px">
  <svg width="30" height="30" viewBox="0 0 30 30"><circle cx="15" cy="15" r="12" fill="var(--blue)"/></svg>
  <div class="post-kicker">A Little Bird Told Me</div>
  <div class="post-title">5 Reasons for Tweeting</div>
  <p class="post-text">There's a thin red line between social media use and networking.</p>
  <div class="btn">Read More <svg width="6" height="8" viewBox="0 0 6 8"><path d="M1 1l4 3-4 3" fill="none" stroke="#fff" stroke-width="1.6"/></svg></div>
</article>

<article class="post abs" style="left:613px;top:1830px">
  <svg width="36" height="36" viewBox="0 0 36 36"><path d="M7 16A11 11 0 0 1 27 11M29 20A11 11 0 0 1 9 25" fill="none" stroke="var(--blue)" stroke-width="4"/><path d="M24 5l6 6-8 2zM12 31l-6-6 8-2z" fill="var(--blue)"/></svg>
  <div class="post-kicker">The Revolution Will Now</div>
  <div class="post-title">Be Optimized</div>
  <p class="post-text">With the advancement of technology, the Internet, and search engines, companies..</p>
  <div class="btn">Read More <svg width="6" height="8" viewBox="0 0 6 8"><path d="M1 1l4 3-4 3" fill="none" stroke="#fff" stroke-width="1.6"/></svg></div>
</article>

<article class="post abs" style="left:147px;top:2145px">
  <svg width="24" height="36" viewBox="0 0 24 36"><rect x="2" y="2" width="20" height="32" rx="3" fill="none" stroke="var(--blue)" stroke-width="3"/><circle cx="12" cy="28" r="2" fill="var(--blue)"/></svg>
  <div class="post-kicker">Searchway's Fast-Loading Tech Encourages</div>
  <div class="post-title">New Standard for Mobile Platforms</div>
  <p class="post-text">Do you ever feel frustrated waiting for pages to load on your phone? You are not the only one.</p>
  <div class="btn">Read More <svg width="6" height="8" viewBox="0 0 6 8"><path d="M1 1l4 3-4 3" fill="none" stroke="#fff" stroke-width="1.6"/></svg></div>
</article>

<article class="post abs" style="left:613px;top:2148px">
  <svg width="40" height="32" viewBox="0 0 40 32"><rect x="2" y="8" width="36" height="22" rx="3" fill="var(--blue)"/><path d="M14 8V4h12v4" fill="none" stroke="var(--blue)" stroke-width="3"/><path d="M2 18h36" stroke="#fff" stroke-width="2"/></svg>
  <div class="post-kicker">Take Your Business to the</div>
  <div class="post-title">Next Level: TMX Edition</div>
  <p class="post-text">Each March, thousands flock to Austin, Texas for the annual Trail Mix Expo (TMX).</p>
  <div class="btn">Read More <svg width="6" height="8" viewBox="0 0 6 8"><path d="M1 1l4 3-4 3" fill="none" stroke="#fff" stroke-width="1.6"/></svg></div>
</article>

<!-- footer -->
<footer class="site-footer abs"></footer>
<p class="follow abs center" style="color:#fff">Follow us on</p>
<span class="social abs" style="left:542px;background:#3b5ba6"></span>
<span class="social abs" style="left:594px;background:#1ea0e0"></span>
<span class="social abs" style="left:642px;background:#e0553f"></span>
<p class="footer-nav abs center" style="color:#fff">Home &nbsp;|&nbsp; Marketing Catalysts &nbsp;|&nbsp; Our Formula &nbsp;|&nbsp; Chemical Reactions &nbsp;|&nbsp; Contact us</p>
<p class="copyright abs center" style="color:#fff">Copyrights @ 2016 all rights reserved</p>

</body>
</html>
```